Copperleaf Roofing Business Card

This is my current business card. But I’d like to make some changes. Somewhere on the card I’d like to list some of the services we offer. Maybe on the back? But I’d still like to keep the red. White and black modern look.

-residential & commercial roofing
-Roof Repairs & Maintenance
-Storm Damage & Insurance Claims specialist
-Christmas Lights and permanent Christmas lights
Fencing. Windows. Gutters. Siding. Sheetrock, painting.

```html
<!DOCTYPE html>
<html lang="en">
<head>
<meta charset="UTF-8">
<title>Copperleaf Roofing Business Card</title>
<link href="https://fonts.googleapis.com/css2?family=Michroma&family=Oswald:wght@500&family=Open+Sans:wght@400;600&display=swap" rel="stylesheet">
<style>
  :root{
    --bg:#3a3a3c;
    --black:#050505;
    --red:#e0262b;
    --deep-red:#7a0f12;
    --white:#ffffff;
    --rule:#5a5a5a;
  }
  *{box-sizing:border-box;margin:0;padding:0}
  html,body{width:1200px;height:1200px;overflow:hidden;background:var(--bg)}
  .canvas{width:1200px;height:1200px;position:relative}
  .card{position:absolute;left:150px;width:900px;height:514px;border-radius:34px;overflow:hidden}
  .card-back{top:60px;background:var(--black)}
  .card-front{top:626px}

  /* back side */
  .brand{position:absolute;left:60px;top:70px;width:330px;text-align:center}
  .brand-dot{width:120px;height:120px;border-radius:50%;border:5px solid var(--white);background:var(--red);margin:0 auto 22px}
  .brand-name{font-family:"Michroma",sans-serif;font-size:24px;line-height:1.35;color:var(--red);letter-spacing:1px}
  .divider{position:absolute;height:1px;background:var(--rule)}
  .divider-left{left:60px;top:300px;width:400px}
  .divider-right{left:470px;top:230px;width:380px}
  .person{position:absolute;left:60px;top:325px}
  .person-name{font-family:"Michroma",sans-serif;font-size:36px;color:var(--white);letter-spacing:1px}
  .person-name .first{color:var(--red)}
  .person-role{font-family:"Open Sans",sans-serif;font-size:22px;color:var(--white);margin-top:6px}
  .person-role .place{color:var(--red)}
  .services{position:absolute;left:470px;top:60px;list-style:none;font-family:"Oswald",sans-serif;font-size:17px;color:var(--white);text-transform:uppercase;line-height:1.55}
  .services .sep,.services li::before{color:var(--red)}
  .services li::before{content:"• "}
  .contact{position:absolute;left:470px;top:252px;list-style:none;font-family:"Open Sans",sans-serif;font-size:21px;color:var(--white);line-height:1.9}
  .contact li{display:flex;align-items:center;gap:12px;letter-spacing:1px}
  .contact svg{width:22px;height:22px;flex:none}
  .tartan-band{position:absolute;left:0;bottom:0;width:100%;height:70px;background:linear-gradient(90deg,var(--deep-red),var(--red) 40%,var(--black) 60%,var(--red))}

  /* front side */
  .tartan-field{position:absolute;inset:0;background:linear-gradient(135deg,var(--red) 0%,var(--deep-red) 35%,var(--black) 55%,var(--red) 80%,var(--deep-red) 100%)}
  .front-brand{position:absolute;left:0;right:0;top:90px;text-align:center}
  .front-brand .brand-dot{width:170px;height:170px;margin-bottom:30px}
  .front-brand .brand-name{font-size:40px;color:var(--white)}
</style>
</head>
<body>
<div class="canvas">

  <section class="card card-back">
    <div class="brand">
      <div class="brand-dot"></div>
      <div class="brand-name">COPPERLEAF<br>ROOFING CO.</div>
    </div>

    <ul class="services">
      <li>Residential &amp; Commercial Roofing</li>
      <li>Roof Repairs &amp; Maintenance</li>
      <li>Storm Damage &amp; Insurance Claims Specialist</li>
      <li>Christmas Lights and Permanent Christmas Lights</li>
      <li>Fencing <span class="sep">•</span> Windows <span class="sep">•</span> Gutters</li>
      <li>Siding <span class="sep">•</span> Sheetrock <span class="sep">•</span> Painting.</li>
    </ul>

    <div class="divider divider-right"></div>

    <ul class="contact">
      <li><svg viewBox="0 0 24 24"><path fill="#e0262b" d="M6.6 10.8a15 15 0 0 0 6.6 6.6l2.2-2.2c.3-.3.7-.4 1-.2 1.1.4 2.3.6 3.6.6.6 0 1 .4 1 1V20c0 .6-.4 1-1 1A17 17 0 0 1 3 4c0-.6.4-1 1-1h3.5c.6 0 1 .4 1 1 0 1.3.2 2.5.6 3.6.1.3 0 .7-.2 1z"/></svg>555-201-4837</li>
      <li><svg viewBox="0 0 24 24"><rect x="2" y="5" width="20" height="14" fill="#e0262b"/><path d="M2 5l10 8 10-8" fill="none" stroke="#050505" stroke-width="1.6"/></svg>reid@copperleafroofing.co</li>
      <li><svg viewBox="0 0 24 24"><g fill="none" stroke="#e0262b" stroke-width="1.8"><circle cx="12" cy="12" r="9"/><ellipse cx="12" cy="12" rx="4" ry="9"/><path d="M3 12h18M5 7h14M5 17h14"/></g></svg>www.copperleafroofing.co</li>
    </ul>

    <div class="divider divider-left"></div>

    <div class="person">
      <div class="person-name"><span class="first">REID</span> CALDER</div>
      <div class="person-role">Roofing contractor in <span class="place">Texas</span></div>
    </div>

    <div class="tartan-band" role="img" aria-label="Red, black and white tartan plaid strip"></div>
  </section>

  <section class="card card-front">
    <div class="tartan-field" role="img" aria-label="Red, black and white tartan plaid background"></div>
    <div class="front-brand">
      <div class="brand-dot"></div>
      <div class="brand-name">COPPERLEAF<br>ROOFING CO.</div>
    </div>
  </section>

</div>
</body>
</html>
```